New Business Card Design Project

We require a business card design for Vexalund, a newly established Indian company.
Our focus is on the development, manufacturing, and export of a diverse array of pharmaceutical products on a global scale. The card should convey a professional appearance, as our primary markets are in Africa, China, and Southeast Asian nations.
We envision a two-sided business card, with the reverse side dedicated to a logo set against a solid color or an elegantly designed pattern. The corners should be rounded. We would appreciate seeing both horizontal and vertical design options. We trust the designer to utilize their expertise in creating this design.

The content for the business card is included in the attached Word file.

Target Market(s)

Our primary markets are in Africa, China, and Southeast Asian, Latin America, Maldives, Sri Lanka

Industry/Entity Type

Pharmaceutical Manufacturing and Export

Contact Information for Business Card

Colors

Designer to choose colors to be used in the design.

Requirements
Must have
• The reverse side of the business card features solely the logo along with the tagline, "Care Beyond Borders."
Should not have
• The logo should not exceed two instances, encompassing both the front and back sides of the card.

```html
<!DOCTYPE html>
<html lang="en">
<head>
<meta charset="utf-8">
<title>Vexalund Business Card</title>
<link href="https://fonts.googleapis.com/css2?family=Montserrat:wght@400;700;800&family=Open+Sans:wght@400;600&display=swap" rel="stylesheet">
<style>
  :root {
    --stage: #222222;
    --card: #ffffff;
    --brand-blue: #2ea8e0;
    --brand-coral: #f0624d;
    --ink: #1c1c1c;
  }
  html, body {
    margin: 0;
    padding: 0;
    width: 1200px;
    height: 711px;
    overflow: hidden;
    background: var(--stage);
  }
  .canvas {
    position: relative;
    width: 1200px;
    height: 711px;
  }
  .card {
    position: absolute;
    top: 205px;
    width: 525px;
    height: 300px;
    background: var(--card);
    border-radius: 18px;
    overflow: hidden;
    box-shadow: 0 0 0 3px var(--brand-blue), 0 14px 30px rgba(0,0,0,.6);
  }
  .card--back { left: 45px; }
  .card--front { left: 630px; }

  /* Back side */
  .back-brand {
    position: absolute;
    left: 0; right: 0; top: 100px;
    display: flex;
    justify-content: center;
    align-items: center;
    gap: 12px;
  }
  .brand-dot {
    width: 20px; height: 20px;
    border-radius: 50%;
    background: var(--brand-coral);
  }
  .brand-name {
    font-family: "Montserrat", sans-serif;
    font-weight: 800;
    color: var(--brand-blue);
    letter-spacing: -0.5px;
    line-height: 1;
  }
  .back-brand .brand-name { font-size: 62px; }
  .tagline {
    position: absolute;
    left: 0; right: 0; top: 182px;
    margin: 0;
    text-align: center;
    font-family: "Montserrat", sans-serif;
    font-size: 14px;
    font-weight: 400;
    color: var(--ink);
    letter-spacing: 0.5px;
  }

  /* Front side */
  .front-wave { position: absolute; inset: 0; }
  .name-tab {
    position: absolute;
    right: 0; top: 18px;
    width: 16px; height: 42px;
    background: var(--brand-blue);
  }
  .person {
    position: absolute;
    right: 26px; top: 18px;
    text-align: right;
    font-family: "Montserrat", sans-serif;
  }
  .person-name {
    font-size: 24px;
    color: var(--brand-blue);
    line-height: 1.1;
  }
  .person-name b { font-weight: 800; }
  .person-name span { font-weight: 400; }
  .person-role {
    font-size: 12px;
    font-weight: 400;
    color: var(--ink);
  }
  .front-brand {
    position: absolute;
    left: 34px; top: 66px;
    display: flex;
    align-items: center;
    gap: 10px;
  }
  .front-brand .brand-name { font-size: 40px; }
  .front-brand .brand-dot { width: 14px; height: 14px; }
  .contacts {
    position: absolute;
    left: 40px; top: 150px;
    margin: 0; padding: 0;
    list-style: none;
    font-family: "Open Sans", sans-serif;
    font-size: 14px;
    color: var(--ink);
  }
  .contacts li {
    display: flex;
    align-items: center;
    gap: 10px;
    height: 24px;
  }
  .contacts svg { width: 16px; height: 16px; flex: none; }
  .address {
    position: absolute;
    left: 340px; top: 186px;
    margin: 0;
    font-family: "Open Sans", sans-serif;
    font-size: 13px;
    line-height: 1.5;
    color: var(--card);
  }
</style>
</head>
<body>
<main class="canvas">

  <section class="card card--back" aria-label="Card reverse side">
    <div class="back-brand">
      <span class="brand-name">Vexalund</span>
      <span class="brand-dot"></span>
    </div>
    <p class="tagline">Care Beyond Borders.</p>
  </section>

  <section class="card card--front" aria-label="Card front side">
    <svg class="front-wave" viewBox="0 0 525 300" preserveAspectRatio="none" aria-hidden="true">
      <path d="M0 258 C100 274 200 268 262 236 C200 276 100 286 0 272 Z" fill="var(--brand-coral)"/>
      <path d="M0 282 C120 292 235 282 300 210 C360 148 420 124 525 116 L525 300 L0 300 Z" fill="var(--brand-blue)"/>
    </svg>

    <div class="name-tab"></div>
    <div class="person">
      <div class="person-name"><b>Arjun</b> <span>K. Malvade</span></div>
      <div class="person-role">CEO</div>
    </div>

    <div class="front-brand">
      <span class="brand-name">Vexalund</span>
      <span class="brand-dot"></span>
    </div>

    <ul class="contacts">
      <li>
        <svg viewBox="0 0 16 16" aria-hidden="true"><rect x="4" y="1.5" width="8" height="13" rx="1.5" fill="none" stroke="var(--brand-coral)" stroke-width="1.6"/></svg>
        +91 98765 43210
      </li>
      <li>
        <svg viewBox="0 0 16 16" aria-hidden="true"><circle cx="8" cy="8" r="6.5" fill="none" stroke="var(--brand-blue)" stroke-width="1.6"/><path d="M1.5 8h13M8 1.5c-3 3.5-3 9.5 0 13M8 1.5c3 3.5 3 9.5 0 13" fill="none" stroke="var(--brand-blue)" stroke-width="1.2"/></svg>
        www.vexalund.com
      </li>
      <li>
        <svg viewBox="0 0 16 16" aria-hidden="true"><rect x="1.5" y="3.5" width="13" height="9" rx="1" fill="var(--brand-coral)"/><path d="M1.5 4l6.5 5 6.5-5" fill="none" stroke="#fff" stroke-width="1.2"/></svg>
        amalvade@vexalund.com
      </li>
    </ul>

    <p class="address">14, Suryakant Nagar,<br>Nashik, 422011, India</p>
  </section>

</main>
</body>
</html>
```